Modern Verdell Tree Care Website

I need a website for a full service Tree Care company. The company provides tree pruning, tree removal, tree preservation, emergency services, stump grinding, and emergency tree services.

Target Market(s)

Customers that need tree services

Industry/Entity Type

Landscaping, Tree Services

Coding

Coded - Design and coding required

Number of Pages Required

5+ page

Font styles to use
Sans Serif

Requirements
Must have
• Good clean design that showcases the services the company provides.
Nice to have
• Services page; contact form, blog, home page, about page

```html
<!DOCTYPE html>
<html lang="en">
<head>
<meta charset="utf-8">
<title>Verdell Tree Care</title>
<link href="https://fonts.googleapis.com/css2?family=Montserrat:wght@400;500;600;700;800&display=swap" rel="stylesheet">
<style>
:root{
  --orange:#f6ac3b;
  --orange-deep:#f39c1f;
  --green:#8dc63f;
  --heading:#56606a;
  --text:#444b52;
  --navy:#141a2e;
  --white:#ffffff;
  --field-border:#e3e3e3;
}
*{box-sizing:border-box;margin:0;padding:0}
html,body{width:1200px;height:4121px;overflow:hidden}
body{font-family:'Montserrat',sans-serif;color:var(--text);background:var(--white)}
.page{position:relative;width:1200px;height:4121px;overflow:hidden}

/* header */
.site-header{position:absolute;left:0;top:0;width:1200px;height:77px;background:var(--white);z-index:3}
.brand{position:absolute;display:flex;align-items:center;gap:10px}
.brand-mark{width:32px;height:32px;background:var(--green);flex:none}
.brand-name{font-family:'Montserrat',sans-serif;font-weight:800;color:var(--heading);letter-spacing:.5px;line-height:1;white-space:nowrap}
.site-header .brand{left:110px;top:22px}
.site-header .brand-name{font-size:19px}
.main-nav{position:absolute;top:28px;left:0;font-size:15px;color:var(--text)}
.main-nav a{position:absolute;white-space:nowrap;color:inherit;text-decoration:none}
.nav-cta{position:absolute;left:976px;top:19px;width:112px;height:39px;background:var(--orange);color:var(--white);font-weight:600;font-size:16px;display:flex;align-items:center;justify-content:center}

/* hero */
.hero{position:absolute;left:0;top:77px;width:1200px;height:667px;
  background:linear-gradient(100deg,#3a2a1c 0%,#4f4024 35%,#5c5a2c 60%,#8a4a2a 80%,#6b3b22 100%);
  clip-path:polygon(0 0,1200px 0,1200px 555px,0 667px)}
.hero-overlay{position:absolute;inset:0;background:linear-gradient(90deg,rgba(0,0,0,.45),rgba(0,0,0,0) 65%)}
.hero-eyebrow{position:absolute;left:110px;top:174px;color:var(--green);font-weight:700;font-size:15px}
.hero-title-small{position:absolute;left:110px;top:216px;color:var(--white);font-weight:800;font-size:32px;letter-spacing:1px}
.hero-title{position:absolute;left:110px;top:258px;color:var(--white);font-weight:800;font-size:46px}
.hero-text{position:absolute;left:110px;top:326px;width:510px;color:var(--white);font-size:15.5px;line-height:30px}
.btn{position:absolute;display:flex;align-items:center;justify-content:center;font-weight:600;font-size:17px;text-transform:uppercase}
.btn-solid{background:var(--orange);color:var(--white)}
.btn-outline{border:2px solid var(--white);color:var(--white)}

.tree-art{position:absolute;border-radius:50% 50% 10% 10%;background:radial-gradient(circle at 50% 40%,#4e8a2e,#2f5e1d 70%,rgba(255,255,255,0) 72%)}

/* about */
.about-photo{position:absolute;left:110px;top:813px;width:397px;height:397px;background:linear-gradient(150deg,#6b4a2c,#3b2a1a 60%,#7a3a1e)}
.section-title{position:absolute;font-weight:800;font-size:35px;color:var(--heading);text-transform:uppercase;letter-spacing:1px}
.about-text{position:absolute;left:578px;top:864px;width:530px;font-size:14px;line-height:33.5px;color:var(--text)}

/* services */
.services{position:absolute;left:0;top:1277px;width:1200px;height:617px;background:linear-gradient(180deg,#f3b640 0%,#f5b84a 50%,#e9b83b 100%)}
.service-card{position:absolute;top:144px;height:294px;background:var(--white);border-radius:4px;text-align:center}
.service-icon{position:absolute;left:50%;top:28px;width:86px;height:86px;margin-left:-43px;border-radius:8px;background:linear-gradient(135deg,#fbd9a0,#f6ac3b)}
.service-card h3{position:absolute;left:0;right:0;top:128px;font-size:19px;font-weight:700;color:#222;letter-spacing:1px}
.service-card p{position:absolute;left:30px;right:30px;top:160px;font-size:15px;line-height:25.5px;color:#555}
.service-link{position:absolute;left:0;right:0;top:249px;font-size:13.5px;font-weight:600;color:#222}
.btn-white{background:var(--white);color:var(--orange);font-size:17px}

/* contact */
.field{position:absolute;border:1px solid var(--field-border);box-shadow:0 2px 8px rgba(0,0,0,.08);background:var(--white);font-size:15.5px;color:#1f3b57;padding-left:32px;display:flex;align-items:center}
.field-message{align-items:flex-start;padding-top:36px}

/* why */
.why{position:absolute;left:0;top:2485px;width:1200px;height:581px;background:linear-gradient(90deg,#3e4550 0%,#6a6f74 45%,#7a5244 70%,#5c6265 100%)}
.why-overlay{position:absolute;inset:0;background:linear-gradient(90deg,rgba(10,12,20,.55),rgba(0,0,0,0) 60%)}
.why h2{position:absolute;left:112px;top:62px;color:var(--white);font-weight:800;font-size:37px;letter-spacing:1px}
.why-list{position:absolute;left:112px;top:154px;list-style:none}
.why-list li{color:var(--white);font-weight:700;font-size:19.5px;letter-spacing:.8px;height:51.3px;display:flex;align-items:flex-start}
.why-list li::before{content:"";width:7px;height:7px;border-radius:50%;background:var(--white);margin:9px 18px 0 0}

/* blog */
.blog-card{position:absolute;top:3221px;width:261px;height:355px;background:var(--white);box-shadow:0 3px 12px rgba(0,0,0,.1)}
.blog-photo{height:142px}
.blog-date{position:absolute;left:19px;top:160px;font-size:12px;color:#444;display:flex;align-items:center;gap:8px}
.blog-date span.cal{width:12px;height:11px;border:1.5px solid #777}
.blog-card h4{position:absolute;left:19px;top:182px;font-size:18px;font-weight:700;color:var(--orange)}
.blog-card p{position:absolute;left:19px;right:12px;top:215px;font-size:10.8px;line-height:20.5px;color:#333}
.read-more{position:absolute;left:19px;top:307px;height:22px;padding:0 12px;border:1px solid #ccc;border-radius:12px;font-size:8.5px;font-weight:700;display:flex;align-items:center;color:#222}

/* footer */
.site-footer{position:absolute;left:0;top:3688px;width:1200px;height:433px;background:var(--navy);clip-path:polygon(0 107px,1200px 0,1200px 433px,0 433px)}
.site-footer .brand{left:0;width:1200px;justify-content:center;top:120px;gap:16px}
.site-footer .brand-mark{width:56px;height:56px}
.site-footer .brand-name{font-size:32px;color:#8a93a0}
.contact-row{position:absolute;top:235px;left:0;width:1200px;color:var(--white);font-size:16px}
.contact-item{position:absolute;display:flex;align-items:center;gap:14px;white-space:nowrap}
.contact-icon{width:38px;height:38px;border-radius:50%;display:flex;align-items:center;justify-content:center;flex:none}
.footer-nav{position:absolute;top:309px;left:0;width:1200px;color:var(--white);font-size:17.5px}
.footer-nav span{position:absolute;white-space:nowrap}
.footer-rule{position:absolute;left:112px;top:371px;width:976px;height:1px;background:#5b6170}
.copyright{position:absolute;left:112px;top:392px;color:var(--white);font-size:16px}
.copyright b{color:var(--orange);font-weight:500}
.social{position:absolute;top:386px;width:32px;height:32px;border-radius:50%;background:var(--white)}
</style>
</head>
<body>
<div class="page">

  <header class="site-header">
    <div class="brand"><span class="brand-mark"></span><span class="brand-name">VERDELL TREE CARE</span></div>
    <nav class="main-nav">
      <a style="left:424px">Home</a>
      <a style="left:509px">About Us</a>
      <a style="left:616px">Our Services</a>
      <a style="left:749px">Blog</a>
      <a style="left:826px">Why Choose Us</a>
    </nav>
    <div class="nav-cta">CONTACT</div>
  </header>

  <section class="hero" role="img" aria-label="Arborist in safety helmet cutting a log with a chainsaw in a forest">
    <div class="hero-overlay"></div>
    <div class="hero-eyebrow">CALL VERDELL FOR ALL YOUR TREE CARE NEEDS</div>
    <div class="hero-title-small">WELCOME TO</div>
    <h1 class="hero-title">VERDELL TREE CARE.</h1>
    <p class="hero-text">Lorem ipsum dolor sit amet, consectetur adipiscing elit, sed do eiusmod tempor incididunt ut labore et dolore magna aliqua. Ut enim ad minim veniam.</p>
    <div class="btn btn-solid" style="left:110px;top:443px;width:181px;height:46px">Get Started</div>
    <div class="btn btn-outline" style="left:307px;top:443px;width:181px;height:46px">Contact Now</div>
  </section>

  <div class="tree-art" style="left:952px;top:672px;width:216px;height:184px" role="img" aria-label="Illustration of a leafy green tree"></div>

  <div class="about-photo" role="img" aria-label="Arborist cutting timber with a chainsaw among trees"></div>
  <h2 class="section-title" style="left:578px;top:808px">About Us</h2>
  <p class="about-text">At Verdell Tree Care, we are more than just a tree service company, we are stewards of our beautiful trees. With a passion deeply rooted in arboriculture, we embark on a mission to promote the health, beauty, and safety of your trees and landscapes. Whether it's expert tree trimming to enhance aesthetics, meticulous tree removal to mitigate hazards, or comprehensive tree health assessments to ensure safety, we approach each task with unwavering dedication and attention to detail.</p>
  <div class="btn btn-solid" style="left:578px;top:1157px;width:180px;height:46px">Click Here</div>

  <section class="services" role="img" aria-label="Golden field and trees at sunset behind the services">
    <h2 class="section-title" style="left:0;width:1200px;top:60px;text-align:center;color:var(--white)">Our Services</h2>
    <div class="service-card" style="left:85px;width:277px">
      <div class="service-icon" role="img" aria-label="Chainsaw and logs icon"></div>
      <h3>TREE PRESERVATION</h3>
      <p>Lorem Ipsum is simply dummy text of the printing and typesetting industry.</p>
      <div class="service-link">CLICK HERE &rarr;</div>
    </div>
    <div class="service-card" style="left:453px;width:275px">
      <div class="service-icon" role="img" aria-label="Cut log icon"></div>
      <h3>TREE REMOVAL</h3>
      <p>Lorem Ipsum is simply dummy text of the printing and typesetting industry.</p>
      <div class="service-link">CLICK HERE &rarr;</div>
    </div>
    <div class="service-card" style="left:818px;width:276px">
      <div class="service-icon" role="img" aria-label="Axe in a stump icon"></div>
      <h3>TREE TRIMMING</h3>
      <p>Lorem Ipsum is simply dummy text of the printing and typesetting industry.</p>
      <div class="service-link">CLICK HERE &rarr;</div>
    </div>
    <div class="btn btn-white" style="left:509px;top:493px;width:181px;height:46px">VIEW ALL</div>
  </section>

  <h2 class="section-title" style="left:0;width:1200px;top:1952px;text-align:center">Contact Us</h2>
  <div class="field" style="left:160px;top:2029px;width:418px;height:53px">First Name</div>
  <div class="field" style="left:621px;top:2029px;width:419px;height:53px">Last Name</div>
  <div class="field" style="left:160px;top:2114px;width:418px;height:51px">E-mail</div>
  <div class="field" style="left:621px;top:2114px;width:419px;height:51px">Phone</div>
  <div class="field field-message" style="left:158px;top:2200px;width:882px;height:136px">Message</div>
  <div class="btn btn-solid" style="left:390px;top:2371px;width:420px;height:42px;font-size:16px">Send Message</div>

  <section class="why" role="img" aria-label="Arborist in plaid shirt beside a felled tree trunk next to a house">
    <div class="why-overlay"></div>
    <h2>WHY CHOOSE US</h2>
    <ul class="why-list">
      <li>LICENSED AND INSURED</li>
      <li>24-HOURS EMERGENCY SERVICES</li>
      <li>LOCALLY OWNED &amp; OPERATED</li>
      <li>PROFESSIONAL WORK</li>
      <li>SAFETY IS OUR NO.1 PRIORITY</li>
      <li>FREE ESTIMATES</li>
      <li>LICENSED ARBORIST ON STAFF</li>
    </ul>
  </section>

  <h2 class="section-title" style="left:0;width:1200px;top:3133px;text-align:center">Latest Blog</h2>
  <article class="blog-card" style="left:128px">
    <div class="blog-photo" role="img" aria-label="Arborist cutting branches in a green tree" style="background:linear-gradient(135deg,#4f7a2a,#7aa34a 60%,#3e5a22)"></div>
    <div class="blog-date"><span class="cal"></span>June-12-2024</div>
    <h4>Lorem ipsum</h4>
    <p>Lorem ipsum dolor sit amet, consectetur adipiscing elit, sed do eiusmod tempor incididunt ut labore et dolore magna aliqua. Ut enim ad minim veniam.</p>
    <div class="read-more">READ MORE &rarr;</div>
  </article>
  <article class="blog-card" style="left:469px">
    <div class="blog-photo" role="img" aria-label="Climber working on a tall tree trunk" style="background:linear-gradient(135deg,#8a8a8a,#cfcfcf 60%,#6b5a4a)"></div>
    <div class="blog-date"><span class="cal"></span>June-12-2024</div>
    <h4>Lorem ipsum</h4>
    <p>Lorem ipsum dolor sit amet, consectetur adipiscing elit, sed do eiusmod tempor incididunt ut labore et dolore magna aliqua. Ut enim ad minim veniam.</p>
    <div class="read-more">READ MORE &rarr;</div>
  </article>
  <article class="blog-card" style="left:811px">
    <div class="blog-photo" role="img" aria-label="Two tree workers in orange safety gear" style="background:linear-gradient(135deg,#4a6a34,#d9822e 55%,#5e7a3c)"></div>
    <div class="blog-date"><span class="cal"></span>June-12-2024</div>
    <h4>Lorem ipsum</h4>
    <p>Lorem ipsum dolor sit amet, consectetur adipiscing elit, sed do eiusmod tempor incididunt ut labore et dolore magna aliqua. Ut enim ad minim veniam.</p>
    <div class="read-more">READ MORE &rarr;</div>
  </article>
  <div class="btn btn-solid" style="left:509px;top:3619px;width:181px;height:45px">VIEW ALL</div>

  <footer class="site-footer">
    <div class="brand"><span class="brand-mark"></span><span class="brand-name">VERDELL TREE CARE</span></div>
    <div class="contact-row">
      <div class="contact-item" style="left:277px">
        <span class="contact-icon" style="background:var(--orange)"><svg width="18" height="18" viewBox="0 0 24 24"><path d="M6.6 10.8a15 15 0 0 0 6.6 6.6l2.2-2.2c.3-.3.7-.4 1-.2 1.1.4 2.3.6 3.6.6.6 0 1 .4 1 1V20c0 .6-.4 1-1 1A17 17 0 0 1 3 4c0-.6.4-1 1-1h3.5c.6 0 1 .4 1 1 0 1.3.2 2.5.6 3.6.1.3 0 .7-.2 1z" fill="#fff"/></svg></span>(555) 214-3870
      </div>
      <div class="contact-item" style="left:498px">
        <span class="contact-icon" style="background:var(--green)"><svg width="20" height="16" viewBox="0 0 20 16"><rect x="1" y="1" width="18" height="14" fill="none" stroke="#fff" stroke-width="2"/><path d="M1 1l9 7 9-7" fill="none" stroke="#fff" stroke-width="2"/></svg></span>hello@verdelltree.com
      </div>
      <div class="contact-item" style="left:770px">
        <span class="contact-icon" style="background:var(--orange)"><svg width="18" height="18" viewBox="0 0 20 20"><rect x="5" y="2" width="10" height="5" fill="#fff"/><rect x="2" y="7" width="16" height="7" rx="1" fill="#fff"/><rect x="5" y="12" width="10" height="6" fill="#fff" stroke="#f6ac3b"/></svg></span>(555) 214-3871
      </div>
    </div>
    <div class="footer-nav">
      <span style="left:150px">Home</span><span style="left:238px">|</span>
      <span style="left:276px">About Us</span><span style="left:377px">|</span>
      <span style="left:431px">Our Services</span><span style="left:575px">|</span>
      <span style="left:614px">Blog</span><span style="left:686px">|</span>
      <span style="left:732px">Why Choose Us</span><span style="left:908px">|</span>
      <span style="left:948px">Contact Us</span>
    </div>
    <div class="footer-rule"></div>
    <div class="copyright">Copyright &copy; 2024 <b>Verdell Tree Care</b>. All Rights Reserved</div>
    <span class="social" style="left:955px" aria-label="Social profile"></span>
    <span class="social" style="left:1003px" aria-label="Video channel"></span>
    <span class="social" style="left:1051px" aria-label="Professional network"></span>
  </footer>

  <div class="tree-art" style="left:8px;top:3608px;width:216px;height:176px" role="img" aria-label="Illustration of a leafy green tree"></div>

</div>
</body>
</html>
```